Calder Vossik - Cinematographer

NEED:
I'm looking for a sleek, professional, modern business card that will give give the recipient the impression that they can trust their production will go smoothly by hiring me. I will bring creativity and knowledge to their shoot, so that we can create powerful images.
I am looking for a card with a strong style and design ethos that could be expanded to a website and a full visual/graphic/design entity for me.
ABOUT ME:
I am a mid-twenties cinematographer, I work on music video, narrative short, commercial, and corporate projects. I blend the science and artistry of cameras and filmmaking to tell a story. I'm an artist, a technician, and a manager.
DESIGN:
I like sleek, simple design. Black, dark grays, white, dark navy, steel blues, I love cyan, but also cyan and red. I am not a fan of earthy tones. I generally prefer modern, san-serif fonts over serifs. My old logo was based on an aperture, a multi-blade device at the back of a lens that controls how much light passes through, but I made it with so many colors, that it doesn't necessarily lend itself to a specific color-scheme or design ethos. I liked that the aperture design provided a sense of the technical requirements of my job. I'm a fan of matte business cards, but am open to plenty of specialty print processes to make an outstanding card.
ATTACHED FILES:
My Old Rainbox Aperture Logo, plus a few designs I've tried playing around with, but am not tied to. I AM OPEN TO NEW DESIGNS, DO NOT FEEL TIED TO THIS.
**I've pulled my old logo down from the attached files, and instead attached other business cards I like, so as not to mislead you where I would like to go.
INFO:
Name: Calder Vossik
Job: Cinematographer
Email: ccvossik@lumenpost.net
Phone: 415.555.0193
Website: caldervossik.com
Updates
I'm adding some images of other cards that I like, and removing my old logo, since I'm looking for something new, and don't want that old logo to push anyone a certain direction.

```html
<!DOCTYPE html>
<html lang="en">
<head>
<meta charset="utf-8">
<title>Calder Vossik – Cinematographer</title>
<link rel="stylesheet" href="https://fonts.googleapis.com/css2?family=Lato:wght@300;400;700&display=swap">
<style>
  :root {
    --page: #ffffff;
    --rim: #ffffff;
    --face-light: #2c2c2c;
    --face-dark: #060606;
    --name-white: #ffffff;
    --title-grey: #9b9b9b;
    --contact-white: #f2f2f2;
  }
  html, body {
    margin: 0;
    padding: 0;
    width: 1200px;
    height: 1038px;
    overflow: hidden;
    background: var(--page);
    font-family: "Lato", Arial, sans-serif;
  }
  .canvas {
    position: relative;
    width: 1200px;
    height: 1038px;
  }
  .card {
    position: absolute;
    left: 57px;
    width: 426px;
    height: 426px;
  }
  .card--front { top: 29px; }
  .card--back  { top: 564px; }
  .card__disc {
    position: absolute;
    inset: 0;
    width: 426px;
    height: 426px;
    filter: drop-shadow(2px 4px 5px rgba(0, 0, 0, 0.45));
  }
  .card__name {
    position: absolute;
    left: 46px;
    margin: 0;
    font-weight: 700;
    font-size: 37px;
    line-height: 1;
    letter-spacing: 0.6px;
    color: var(--name-white);
    text-shadow: 0 0 6px rgba(255, 255, 255, 0.85), 0 0 2px rgba(255, 255, 255, 0.9);
    white-space: nowrap;
  }
  .card__title {
    position: absolute;
    left: 103px;
    margin: 0;
    font-weight: 300;
    font-size: 19px;
    line-height: 1;
    letter-spacing: 6.4px;
    color: var(--title-grey);
    white-space: nowrap;
  }
  .card--front .card__name  { top: 190px; }
  .card--front .card__title { top: 242px; }
  .card--back .card__name   { top: 148px; }
  .card--back .card__title  { top: 203px; }
  .card__contact {
    position: absolute;
    left: 223px;
    top: 233px;
    margin: 0;
    padding: 0;
    list-style: none;
    font-size: 11.5px;
    line-height: 20px;
    color: var(--contact-white);
  }
</style>
</head>
<body>
<main class="canvas">

  <section class="card card--front" aria-label="Card front">
    <svg class="card__disc" viewBox="0 0 426 426">
      <defs>
        <linearGradient id="face-tone-front" x1="0" y1="0" x2="1" y2="1">
          <stop offset="0" stop-color="var(--face-light)"/>
          <stop offset="0.55" stop-color="var(--face-dark)"/>
          <stop offset="1" stop-color="var(--face-dark)"/>
        </linearGradient>
      </defs>
      <circle cx="213" cy="213" r="213" fill="var(--rim)"/>
      <circle cx="213" cy="213" r="203" fill="url(#face-tone-front)" role="img" aria-label="Dark circular face with a film-leader style graphic"/>
    </svg>
    <h1 class="card__name">CALDER VOSSIK</h1>
    <p class="card__title">CINEMATOGRAPHER</p>
  </section>

  <section class="card card--back" aria-label="Card back">
    <svg class="card__disc" viewBox="0 0 426 426">
      <defs>
        <linearGradient id="face-tone-back" x1="0" y1="0" x2="1" y2="1">
          <stop offset="0" stop-color="var(--face-light)"/>
          <stop offset="0.55" stop-color="var(--face-dark)"/>
          <stop offset="1" stop-color="var(--face-dark)"/>
        </linearGradient>
      </defs>
      <circle cx="213" cy="213" r="213" fill="var(--rim)"/>
      <circle cx="213" cy="213" r="203" fill="url(#face-tone-back)" role="img" aria-label="Dark circular face with a film-leader style graphic"/>
    </svg>
    <h2 class="card__name">CALDER VOSSIK</h2>
    <p class="card__title">CINEMATOGRAPHER</p>
    <ul class="card__contact">
      <li>415.555.0193</li>
      <li>ccvossik@lumenpost.net</li>
      <li>www.caldervossik.com</li>
    </ul>
  </section>

</main>
</body>
</html>
```